K7 Services business card design contest. Use logo and create a professional layout.

See attached sample. Please sharpen all text and images, don't want any pix-elated content. We are looking for a clean look that quickly provides the information need. Please include our information provided on the sample card. Please feel free to offer any design changes. Please only user the colors provided: #2D3539 & #FFA500. Do not prefer any images other than the K7 Logo

Target Market(s)

Construction, Architects, General Contractors, residential

Industry/Entity Type

Business

Contact Information for Business Card

Company logo, Name, email, fax & phone

Font styles to use
Other font styles liked:
• Josefin Slab

Requirements
Must have
• Name
• Phone & Fax #'s
• address
• Logo
• Website url: www.kq7services.example
Nice to have
• Font Colors #2D3539 & #FFA400
• We prefer a white background.

```html
<!DOCTYPE html>
<html lang="en">
<head>
<meta charset="utf-8">
<title>K7 Services Business Card</title>
<link href="https://fonts.googleapis.com/css2?family=Montserrat:wght@400;500;700&display=swap" rel="stylesheet">
<style>
  :root {
    --ink: #2D3539;
    --accent: #FFA500;
    --paper: #FFFFFF;
    --backdrop: #E4E4E4;
  }
  * { margin: 0; padding: 0; box-sizing: border-box; }
  html, body { width: 1200px; height: 852px; overflow: hidden; }
  body {
    background: var(--backdrop);
    font-family: "Montserrat", Arial, sans-serif;
    color: var(--ink);
    position: relative;
  }
  .card {
    position: absolute;
    width: 540px;
    height: 310px;
    background: var(--paper);
    border-radius: 12px;
    overflow: hidden;
    box-shadow: 0 6px 18px rgba(0,0,0,0.15);
  }
  .card--front { left: 40px; top: 271px; }
  .card--back { left: 620px; top: 271px; }

  .wordmark { display: flex; flex-direction: column; }
  .wordmark__name { font-weight: 700; color: var(--ink); line-height: 1; }
  .wordmark__tagline { font-weight: 700; color: var(--ink); line-height: 1.1; }

  .card--front .wordmark {
    position: absolute; left: 0; right: 0; top: 110px; align-items: center;
  }
  .card--front .wordmark__name { font-size: 54px; }
  .card--front .wordmark__tagline { font-size: 22px; margin-top: 4px; }

  .card--back .wordmark { position: absolute; right: 34px; top: 30px; align-items: flex-start; }
  .card--back .wordmark__name { font-size: 34px; }
  .card--back .wordmark__tagline { font-size: 14px; margin-top: 2px; }

  .services {
    position: absolute; right: 34px; top: 112px;
    font-size: 12px; letter-spacing: 0.5px; color: var(--ink);
  }
  .divider {
    position: absolute; left: 254px; right: 34px; top: 134px;
    height: 2px; background: var(--accent);
  }
  .person { position: absolute; left: 30px; top: 116px; }
  .person__name { font-size: 18px; color: var(--accent); font-weight: 400; line-height: 1; }
  .person__title { font-size: 12px; margin-top: 10px; }

  .address {
    position: absolute; right: 34px; top: 152px;
    font-size: 11.5px; line-height: 1.6; text-align: right;
  }
  .contacts { position: absolute; left: 30px; top: 190px; list-style: none; }
  .contacts li {
    display: flex; align-items: center; gap: 10px;
    font-size: 12px; line-height: 1.7;
  }
  .contacts svg { width: 12px; height: 12px; flex: none; }

  .band { position: absolute; left: 0; bottom: 0; width: 540px; height: 34px; }
</style>
</head>
<body>

<section class="card card--front" aria-label="Card front">
  <div class="wordmark">
    <span class="wordmark__name">K7 Services</span>
    <span class="wordmark__tagline">The Value of a View</span>
  </div>
</section>

<section class="card card--back" aria-label="Card back">
  <div class="wordmark">
    <span class="wordmark__name">K7 Services</span>
    <span class="wordmark__tagline">The Value of a View</span>
  </div>

  <p class="services">DRONE | WEBCAM | VIDEO</p>
  <div class="divider"></div>

  <div class="person">
    <p class="person__name">Marcus D. Hollins, MBA</p>
    <p class="person__title">Director of Operations</p>
  </div>

  <p class="address">2140 Larkspur Road, Suite<br>210-118 Alder Falls, Georgia, 30000</p>

  <ul class="contacts">
    <li>
      <svg viewBox="0 0 12 12" aria-hidden="true"><path fill="#FFA500" d="M2 1h2l1 3-1.5 1a6 6 0 0 0 3.5 3.5L8 7l3 1v2a1 1 0 0 1-1 1A9 9 0 0 1 1 2a1 1 0 0 1 1-1z"/></svg>
      <span>(555) 013 - 6627</span>
    </li>
    <li>
      <svg viewBox="0 0 12 12" aria-hidden="true"><rect x="3" y="1" width="6" height="4" fill="none" stroke="#FFA500" stroke-width="1.2"/><rect x="1" y="5" width="10" height="6" rx="1" fill="#FFA500"/></svg>
      <span>(555) 019 - 3358</span>
    </li>
    <li>
      <svg viewBox="0 0 12 12" aria-hidden="true"><circle cx="6" cy="6" r="5" fill="#FFA500"/><path d="M1 6h10M6 1c-2 3-2 7 0 10M6 1c2 3 2 7 0 10" stroke="#fff" stroke-width="0.8" fill="none"/></svg>
      <span>www.kq7services.example</span>
    </li>
  </ul>

  <svg class="band" viewBox="0 0 540 34" preserveAspectRatio="none" aria-hidden="true">
    <polygon points="0,22 300,22 318,0 540,0 540,34 0,34" fill="#FFA500"/>
    <polygon points="300,34 330,0 540,0 540,34" fill="#2D3539"/>
  </svg>
</section>

</body>
</html>
```